Stationery for use with Ninefold Ridge reports

I would like to get a stationery design that my firm -- Ninefold Ridge Advisory -- will use as a format for reports that we send our clients. I am specifically looking for a design for use on a piece of paper or letterhead -- not business cards or envelopes.

We are an Africa based US risk intelligence and strategy firm that works with multinational corporations operating in West Africa. Our initial thinking is that we would like a color scheme consistent with our existing logo -- however we are open to other color schemes.

Also, we would like to see at least two separate versions: one with our company name and logo, the other without name and logo.

We also would like font recommendations for the stationary design.

The final design should communicate discreet professionalism and a modern approach, but it should not overshadow the words and information printed on the stationery.

Target Market(s)

Multinational corporations that currently use our products.

Font styles to use
Serif
Sans Serif

Requirements
Must have
• Sense of discreet professionalism that will not overshadow the content we put onto the stationery format.
• We would like to see designs with and without our company name/logo.
• Please suggest fonts that would work with the stationery.
Nice to have
• Ideally colors consistent with out existing logo, though we are open to and even encourage other ideas.
Should not have
• No need for business cards or envelopes.

```html
<!DOCTYPE html>
<html lang="en">
<head>
<meta charset="utf-8">
<title>Ninefold Ridge Advisory — Letterhead</title>
<link href="https://fonts.googleapis.com/css2?family=Open+Sans:wght@400;700&display=swap" rel="stylesheet">
<style>
  :root {
    --backdrop: #e4e4e4;
    --paper: #ffffff;
    --ink: #555a5e;
    --navy: #1f3140;
    --ochre: #e0a94b;
    --sky: #a9d3ea;
    --map-fill: #dfe4e8;
    --sign-fill: #eef0f2;
  }
  * { box-sizing: border-box; margin: 0; padding: 0; }
  html, body {
    width: 1200px; height: 960px; overflow: hidden;
    background: var(--backdrop);
    font-family: "Open Sans", Arial, sans-serif;
  }
  .letterhead {
    position: absolute; left: 300px; top: 54px;
    width: 600px; height: 852px;
    background: var(--paper);
    overflow: hidden;
  }
  .region-map {
    position: absolute; left: 31px; top: 18px;
    width: 77px; height: 83px;
    background: var(--map-fill);
    border-radius: 4px;
  }
  .brand {
    position: absolute; right: 31px; top: 30px;
    display: flex; flex-direction: column; align-items: flex-end; gap: 8px;
  }
  .brand-mark {
    width: 22px; height: 22px; background: var(--ochre);
  }
  .brand-name {
    color: var(--navy); font-weight: 700; font-size: 13px;
    line-height: 16px; text-align: right;
  }
  .header-rule {
    position: absolute; left: 31px; top: 109px;
    width: 537px; height: 2px; background: var(--navy);
  }
  .letter-date {
    position: absolute; left: 59px; top: 254px;
    font-size: 10px; line-height: 16px; color: var(--ink);
  }
  .letter-body {
    position: absolute; left: 59px; top: 302px; width: 490px;
    font-size: 9.9px; line-height: 22.5px; color: var(--ink);
    white-space: nowrap;
  }
  .letter-body p { margin-bottom: 3px; }
  .letter-body span { display: block; }
  .signature {
    position: absolute; left: 416px; top: 594px;
    width: 120px; height: 36px;
    background: var(--sign-fill); border-radius: 3px;
  }
  .signer {
    position: absolute; left: 421px; top: 631px;
    font-size: 9.5px; line-height: 12px; color: var(--ink);
  }
  .footer-band {
    position: absolute; left: 0; bottom: 0; width: 600px; height: 16px;
  }
</style>
</head>
<body>
  <main class="letterhead">
    <div class="region-map" role="img" aria-label="Outline map of Africa"></div>

    <div class="brand">
      <div class="brand-mark"></div>
      <div class="brand-name">Ninefold Ridge Advisory</div>
    </div>

    <div class="header-rule"></div>

    <div class="letter-date">Date, 10 September, 2020</div>

    <div class="letter-body">
      <p>
        <span>This is a sample letter that has been placed to demonstrate typing remat (Your Company). letterhead</span>
        <span>design. When positioned properly, it will serve to work in harmony with all other elements letterhead.</span>
        <span>This letterhead design is meant to project an image</span>
      </p>
      <p>
        <span>This letterhead design is meant project an image of professionalism reliability. By using simple aligen</span>
        <span>we have created a very spacious feeling. The simplicity suggest &nbsp;rengththe spaciousnes contributes h</span>
        <span>aesthetics the layout. These basic qualities along with the (Your Company)</span>
      </p>
      <p>
        <span>look and helps reinforce the (Your Company) brand. letterhead design is meant to project an image p</span>
        <span>design. When positioned properly, it will serve to work in harmony all the other elements letterhead.</span>
        <span>sionalism and reliability.</span>
      </p>
      <p>
        <span>This letterhead design is based on the (Form of your logo) form (Your Company) logo. Each stationery</span>
        <span>we have created a very spacious feeling. The simplicity suggests strength the spaciousnes contribute</span>
        <span>part of the (Form of your logo).</span>
      </p>
    </div>

    <div class="signature" role="img" aria-label="Handwritten signature of Martin Adeyemi"></div>
    <div class="signer">Martin Adeyemi<br>Manager</div>

    <svg class="footer-band" viewBox="0 0 600 16" preserveAspectRatio="none" aria-hidden="true">
      <polygon points="0,0 491,0 483,16 0,16" fill="var(--ochre)"/>
      <polygon points="499,0 600,0 600,16 491,16" fill="var(--sky)"/>
    </svg>
  </main>
</body>
</html>
```